New business card design

I need original, modern, business looking but dzen (minimalistic) looking design.
Also refer to websit travenko.ru

Text is

Веденин Олег, PMP
Партнер

Моб. +7 (915) 604 7189
info@travenko.ru
Москва, Россия, 125493, ул. Берёзовая 27/2
=====================

Vedenin Oleg, PMP
Partner

Mob. +7 (915) 604 7189
info@travenko.ru
Moscow, Russia,125493, Beryozovaya 27/2

```html
<!DOCTYPE html>
<html lang="en">
<head>
<meta charset="utf-8">
<title>Corvella — Business Card</title>
<link href="https://fonts.googleapis.com/css2?family=Exo+2:wght@300;400;600&display=swap" rel="stylesheet">
<style>
  :root {
    --page: #eef0f2;
    --card-white: #fbfbfb;
    --card-grey: #e4e6e8;
    --blue-deep: #1d6db5;
    --blue-mid: #3a8fd3;
    --grey-band-dark: #b9bdc2;
    --grey-band-light: #eceef0;
    --teal: #2fa9d4;
    --ink: #1d3f5e;
    --text-grey: #55606b;
  }
  * { box-sizing: border-box; margin: 0; padding: 0; }
  html, body { width: 1200px; height: 828px; overflow: hidden; }
  body {
    background: var(--page);
    font-family: "Exo 2", sans-serif;
    display: flex;
    align-items: center;
    justify-content: center;
    gap: 40px;
  }
  .card {
    position: relative;
    width: 540px;
    height: 310px;
    background: linear-gradient(160deg, var(--card-white) 30%, var(--card-grey) 100%);
    box-shadow: 0 6px 18px rgba(0,0,0,0.18);
    overflow: hidden;
  }
  .accent-band {
    position: absolute;
    top: 0;
    right: 0;
    width: 290px;
    height: 44px;
    background: linear-gradient(90deg, var(--grey-band-dark), var(--grey-band-light));
  }
  .accent-panel {
    position: absolute;
    top: 0;
    left: 0;
    width: 230px;
    height: 100%;
    background: linear-gradient(160deg, var(--blue-mid), var(--blue-deep));
  }
  .brand {
    position: absolute;
    display: flex;
    align-items: center;
    gap: 12px;
  }
  .brand-mark {
    width: 34px; height: 34px;
    background: var(--teal);
  }
  .brand-name {
    font-weight: 300;
    color: var(--teal);
    letter-spacing: 1px;
    line-height: 1;
  }
  .front .brand { left: 130px; top: 130px; }
  .front .brand-name { font-size: 48px; }
  .back .brand { left: 290px; top: 234px; gap: 9px; }
  .back .brand-mark { width: 24px; height: 24px; }
  .back .brand-name { font-size: 30px; }
  .contact {
    position: absolute;
    right: 24px;
    top: 22px;
    width: 260px;
    text-align: right;
    color: var(--text-grey);
  }
  .person-name {
    font-size: 17px;
    font-weight: 600;
    color: var(--ink);
    letter-spacing: 1.5px;
  }
  .person-role {
    font-size: 11px;
    letter-spacing: 2px;
    margin-top: 2px;
  }
  .address {
    margin-top: 18px;
    font-size: 12px;
    line-height: 1.4;
    color: var(--ink);
  }
  .lines { margin-top: 14px; list-style: none; font-size: 10.5px; line-height: 1.75; }
  .lines li { display: flex; justify-content: flex-end; align-items: center; gap: 6px; }
  .icon { width: 10px; height: 10px; flex: none; }
</style>
</head>
<body>

<section class="card front" aria-label="Card front">
  <div class="accent-band" role="img" aria-label="Decorative grey ribbon accent"></div>
  <div class="brand">
    <span class="brand-mark"></span>
    <span class="brand-name">Corvella</span>
  </div>
</section>

<section class="card back" aria-label="Card back">
  <div class="accent-panel" role="img" aria-label="Decorative blue wave panel"></div>

  <div class="contact">
    <p class="person-name">IVEN DORSK</p>
    <p class="person-role">PARTNER</p>
    <p class="address">12 Example Lane<br>Sampletown</p>
    <ul class="lines">
      <li>+0 (000) 555 0142
        <svg class="icon" viewBox="0 0 10 10"><path d="M2 1 L4 1 L4.6 3 L3.5 3.8 C4 5 5 6 6.2 6.5 L7 5.4 L9 6 L9 8 C5 9 1 5 2 1 Z" fill="var(--ink)"/></svg>
      </li>
      <li>hello@corvella.example
        <svg class="icon" viewBox="0 0 10 10"><rect x="0.5" y="2" width="9" height="6" fill="var(--ink)"/><path d="M0.5 2 L5 5.5 L9.5 2" fill="none" stroke="#fff" stroke-width="0.8"/></svg>
      </li>
      <li>corvella.example
        <svg class="icon" viewBox="0 0 10 10"><circle cx="5" cy="5" r="4.3" fill="none" stroke="var(--ink)" stroke-width="1"/><ellipse cx="5" cy="5" rx="1.8" ry="4.3" fill="none" stroke="var(--ink)" stroke-width="0.8"/><line x1="0.7" y1="5" x2="9.3" y2="5" stroke="var(--ink)" stroke-width="0.8"/></svg>
      </li>
    </ul>
  </div>

  <div class="brand">
    <span class="brand-mark"></span>
    <span class="brand-name">Corvella</span>
  </div>
</section>

</body>
</html>
```